www.marvenholt.com

Updating website so looks futristic but yet business like and easy to navigate, essentially a good landing page with a cool picture summing up what we do, and links to the following pages, all other pages on site to be updated, Exclusive Distributor of Brisk Forge Unique Fitness Equipment Products in UK & Ireland, www.crestvolley.co.uk Exclusive Partners & Distributors Of Crest Volley - Obstacle Races - Obstacle Hire - Obstacle Training - Adventure Events, www.goplumwick.co.uk Adventures That Inspire. We also Health Club / Facillity Consultancy

```html
<!DOCTYPE html>
<html lang="en">
<head>
<meta charset="utf-8">
<title>Marven Holt – Health, Wellness, Fitness, Consultants</title>
<link rel="stylesheet" href="https://fonts.googleapis.com/css2?family=Marcellus+SC&family=Lato:wght@400;700&display=swap">
<style>
:root{
  --green-dark:#1b4a0b;
  --green:#4b8d1d;
  --green-mid:#5a9a24;
  --green-light:#c8f09c;
  --green-pale:#e3f7c9;
  --ink:#222;
  --muted:#555;
  --white:#fff;
  --head:"Marcellus SC", serif;
  --body:"Lato", sans-serif;
}
*{box-sizing:border-box;margin:0;padding:0}
html,body{width:1200px;height:3727px;overflow:hidden;background:var(--white)}
body{position:relative;font-family:var(--body);color:var(--ink)}
section,header,footer{position:absolute;left:0;width:1200px;overflow:hidden}
.photo{position:absolute}

/* hero */
.hero{top:0;height:658px}
.hero .photo{inset:0;background:
  radial-gradient(ellipse 260px 300px at 300px 330px,rgba(236,196,160,.75),rgba(236,196,160,0) 70%),
  radial-gradient(ellipse 200px 260px at 560px 380px,rgba(70,80,60,.55),rgba(70,80,60,0) 70%),
  radial-gradient(ellipse 300px 200px at 120px 200px,rgba(230,240,200,.8),rgba(230,240,200,0) 70%),
  radial-gradient(ellipse 320px 260px at 1000px 420px,rgba(150,110,90,.55),rgba(150,110,90,0) 70%),
  linear-gradient(120deg,#b9d19a 0%,#87a96a 35%,#5f7f49 62%,#8aa577 100%)}
.hero-tint{position:absolute;inset:0;background:rgba(70,140,30,.28)}
.topbar{position:absolute;top:0;left:0;width:1200px;height:99px;border-bottom:1px solid rgba(255,255,255,.6)}
.brand{position:absolute;left:90px;top:20px;color:var(--white)}
.brand-name{font-family:var(--head);font-size:30px;line-height:1}
.brand-tag{font-family:var(--head);font-size:14px;margin-top:6px}
.nav{position:absolute;right:88px;top:36px;display:flex;gap:23px;font-size:16px;color:var(--white);align-items:center}
.video-box{position:absolute;left:621px;top:99px;width:502px;height:559px;background:linear-gradient(180deg,rgba(90,25,30,.62),rgba(60,30,30,.5))}
.video-frame{position:absolute;left:25px;top:20px;right:25px;bottom:0;border:2px solid rgba(255,255,255,.85);border-bottom:none;text-align:center;color:var(--white)}
.video-frame .play{margin-top:50px}
.video-title{font-family:var(--head);font-size:32px;margin-top:20px}
.video-sub{font-size:18px;margin-top:4px}
.video-text{font-size:14px;width:260px;margin:16px auto 0;line-height:1.5}
.btn-light{display:inline-block;background:var(--green-light);color:var(--green-dark);font-family:var(--head);font-size:19px;border-radius:30px;padding:14px 42px;margin-top:28px}

/* welcome */
.welcome{top:658px;height:465px}
.welcome h1{position:absolute;left:77px;top:60px;font-family:var(--head);font-weight:400;font-size:36px;color:#111}
.welcome h1 span{color:var(--green)}
.welcome p{position:absolute;left:77px;top:118px;width:760px;font-size:14px;line-height:1.85;color:var(--muted)}
.btn-green{position:absolute;left:77px;top:346px;width:211px;height:56px;border-radius:30px;background:var(--green);color:var(--white);font-family:var(--head);font-size:19px;display:flex;align-items:center;justify-content:center}
.welcome .product{left:857px;top:37px;width:273px;height:348px;background:
  radial-gradient(ellipse 60px 140px at 140px 130px,rgba(214,170,130,.55),rgba(214,170,130,0) 70%),
  radial-gradient(ellipse 110px 40px at 140px 320px,rgba(90,95,100,.45),rgba(90,95,100,0) 70%),
  linear-gradient(180deg,#ffffff,#f1f3f4)}

/* what we are */
.services{top:1123px;height:541px;background:linear-gradient(90deg,#cfeea7,#e5f8cd 50%,#c9eb9f)}
.section-title{position:absolute;left:0;width:100%;text-align:center;font-family:var(--head);font-weight:400;font-size:34px;color:#111}
.services .section-title{top:62px}
.card{position:absolute;top:189px;height:283px}
.card .photo{left:0;top:0;right:0;height:216px}
.card-label{position:absolute;left:0;right:0;bottom:0;height:67px;background:var(--green);color:var(--white);font-family:var(--head);font-style:italic;font-size:28px;display:flex;align-items:center;justify-content:center}
.card-icon{position:absolute;left:50%;top:-55px;width:96px;height:96px;margin-left:-48px;border-radius:50%;background:var(--white);border:5px solid var(--green-dark);display:flex;align-items:center;justify-content:center}
.ph-run{background:linear-gradient(180deg,#f2f0ec 0%,#c9b8a6 45%,#6d6158 75%,#3a3634 100%)}
.ph-pilates{background:linear-gradient(180deg,#e9eef0 0%,#a9c7c9 35%,#d79a6a 62%,#5b5656 100%)}
.ph-train{background:linear-gradient(120deg,#7aa6c0 0%,#a7c2cf 40%,#e3b15a 70%,#7a5a3c 100%)}

/* team */
.team{top:1664px;height:497px}
.team .section-title{top:62px}
.member{position:absolute;top:144px;width:293px;height:353px}
.member svg.shape{position:absolute;left:0;top:0}
.member-name{position:absolute;top:20px;width:100%;text-align:center;font-family:var(--head);font-size:19px;color:var(--white)}
.member-role{position:absolute;top:50px;width:100%;text-align:center;font-size:12px;color:var(--white);line-height:1.5}
.socials{position:absolute;top:96px;width:100%;display:flex;justify-content:center;gap:10px}
.socials i{width:32px;height:32px;border-radius:50%;background:var(--white);display:block}
.member .photo{left:66px;bottom:0;width:161px;height:170px;border-radius:80px 80px 0 0;background:linear-gradient(180deg,rgba(27,74,11,0) 0%,rgba(150,110,80,.55) 30%,#2a2a2a 55%,#151515 100%)}

/* stats */
.stats{top:2161px;height:161px;background:var(--green)}
.stat{position:absolute;top:40px;width:260px;margin-left:-130px;text-align:center;color:var(--white)}
.stat b{display:block;font-weight:400;font-size:46px;line-height:1}
.stat span{display:block;font-family:var(--head);font-size:21px;margin-top:10px}

/* event + appointment */
.split{top:2322px;height:465px}
.event .photo{left:0;top:0;width:600px;height:465px;background:
  radial-gradient(ellipse 200px 160px at 450px 90px,rgba(120,140,90,.6),rgba(120,140,90,0) 70%),
  linear-gradient(135deg,#4c5a40,#2a3524 55%,#5a6a50)}
.appoint .photo{left:600px;top:0;width:600px;height:465px;background:
  radial-gradient(ellipse 120px 200px at 350px 200px,rgba(220,180,150,.6),rgba(220,180,150,0) 70%),
  radial-gradient(ellipse 120px 200px at 520px 280px,rgba(230,200,80,.45),rgba(230,200,80,0) 70%),
  linear-gradient(135deg,#c9dcc0,#8fb37c 60%,#b9d3a8)}
.appoint-tint{position:absolute;left:600px;top:0;width:600px;height:465px;background:rgba(70,130,40,.42)}
.event-tint{position:absolute;left:0;top:0;width:600px;height:465px;background:rgba(0,0,0,.3)}
.half-title{position:absolute;width:600px;text-align:center;font-family:var(--head);font-weight:400;font-size:32px;color:var(--white);top:62px}
.half-text{position:absolute;width:600px;text-align:center;font-size:13px;color:var(--white);top:108px;line-height:1.7}
.event-card{position:absolute;left:70px;top:197px;width:464px;height:176px;background:rgba(200,240,156,.8);border:1px solid rgba(255,255,255,.6)}
.event-date{position:absolute;left:0;top:0;width:150px;height:176px;border-right:2px solid rgba(255,255,255,.8);text-align:center;color:var(--green)}
.event-date b{display:block;font-weight:400;font-size:50px;margin-top:30px}
.event-date span{font-family:var(--head);font-size:23px}
.event-info{position:absolute;left:172px;top:20px;width:270px}
.event-info h3{font-family:var(--head);font-weight:400;font-size:25px;color:var(--green-dark)}
.event-info p{font-size:13px;color:var(--white);margin-top:8px;line-height:1.5}
.btn-dark{display:inline-block;margin-top:12px;background:var(--green-dark);color:var(--white);font-family:var(--head);font-size:17px;border-radius:24px;padding:9px 18px}
.field{position:absolute;height:44px;background:var(--white);border-radius:22px;font-size:13px;color:#666;padding:13px 18px}
.submit{position:absolute;left:807px;top:361px;width:206px;height:44px;border-radius:22px;background:var(--green-dark);color:var(--white);font-family:var(--head);font-size:19px;display:flex;align-items:center;justify-content:center}

/* blog */
.blog{top:2787px;height:522px}
.blog .section-title{top:55px}
.post{position:absolute;top:149px;width:333px}
.post .photo{position:relative;height:186px}
.ph-b1{background:linear-gradient(120deg,#f2f2f2 0%,#d9d9d9 35%,#cf9c7c 55%,#2d4f8a 80%,#23304a 100%)}
.ph-b2{background:linear-gradient(180deg,#5e5e5e 0%,#9a9a9a 40%,#d8ae8f 62%,#3c3c44 100%)}
.ph-b3{background:linear-gradient(180deg,#8a3b2c 0%,#b9a291 40%,#c29274 65%,#2b2b2b 100%)}
.post-date{position:absolute;left:15px;top:14px;width:60px;height:54px;background:var(--green);border:2px solid var(--white);color:var(--white);text-align:center;font-size:20px;line-height:1.1;padding-top:4px}
.post-date small{display:block;font-size:15px}
.post h4{font-family:var(--head);font-weight:400;font-size:22px;color:var(--green-dark);margin-top:22px}
.post p{font-size:14px;color:var(--muted);line-height:1.9;margin-top:6px}

/* contact */
.contact{top:3309px;height:313px}
.contact .map{left:0;top:0;width:600px;height:313px;background:linear-gradient(135deg,#eef7df,#d6ecb8 60%,#e4f2cf)}
.contact-panel{position:absolute;left:600px;top:0;width:600px;height:313px;background:var(--green-dark);color:var(--white)}
.contact-panel h3{position:absolute;left:243px;top:34px;font-family:var(--head);font-weight:400;font-size:23px}
.contact-list{position:absolute;left:212px;top:87px;list-style:none;font-size:14px}
.contact-list li{display:flex;align-items:flex-start;gap:18px;margin-bottom:14px;line-height:1.5}
.contact-list svg{flex:none;margin-top:2px}

/* footer */
.footer{top:3622px;height:105px;background:var(--green)}
.footer .brand{left:90px;top:26px}
.footer-social{position:absolute;left:515px;top:44px;display:flex;gap:16px}
.footer-social i{display:block;width:15px;height:15px;border-radius:50%;background:var(--green-dark)}
.copyright{position:absolute;left:808px;top:44px;font-size:14px;color:var(--white)}
</style>
</head>
<body>

<header class="hero">
  <div class="photo" role="img" aria-label="Photo of people training on resistance gym machines"></div>
  <div class="hero-tint"></div>
  <div class="topbar">
    <div class="brand"><div class="brand-name">Marven Holt</div><div class="brand-tag">Health, Wellness, Fitness, Consultants</div></div>
    <nav class="nav"><span>Home</span><span>Contact</span><span>Our Team</span><span>Testimonials</span><span>Health</span><span>Wellness</span><span>Fitness</span><span>Brisk Forge</span>
      <svg width="20" height="20" viewBox="0 0 20 20" fill="none" stroke="#fff" stroke-width="2"><circle cx="8" cy="8" r="6"/><line x1="12.5" y1="12.5" x2="18" y2="18"/></svg>
    </nav>
  </div>
  <div class="video-box">
    <div class="video-frame">
      <svg class="play" width="76" height="76" viewBox="0 0 76 76"><circle cx="38" cy="38" r="35" fill="none" stroke="#fff" stroke-width="4"/><polygon points="30,23 54,38 30,53" fill="#fff"/></svg>
      <div class="video-title">Marven Holt</div>
      <div class="video-sub">Health, Wellness, Fitness</div>
      <div class="video-text">Lorem Ipsum is simply dummy text of the printing and typesetting industry.</div>
      <div class="btn-light">Watch Video</div>
    </div>
  </div>
</header>

<section class="welcome">
  <h1>Welcome to <span>Marven Holt</span></h1>
  <p>Marven Holt are leading consultants to the Health, Wellness and Fitness industry, with over 25 years experience working with some of the biggest global worldwide brands from equipment providers and facility operators to mass participation events and obstacle course races. Marven Holt is a multi disciplined business specialising in helping brands grow through insight, strategy creation and valuable sector collaboration, recent clients include the exclusive distribution of Brisk Forge bodyweight training products for the UK and Ireland Marven Holt is a multi disciplined business specialising in helping brands grow through insight, strategy creation and valuable sector collaboration, recent clients include the exclusive distribution of Brisk Forge bodyweight training products for the UK and Ireland.</p>
  <div class="btn-green">Read More</div>
  <div class="photo product" role="img" aria-label="Photo of a woman walking on a fitness stepper machine"></div>
</section>

<section class="services">
  <div class="photo" style="inset:0;background:radial-gradient(ellipse 260px 260px at 900px 120px,rgba(120,170,80,.25),rgba(120,170,80,0) 70%)" role="img" aria-label="Faint background photo of a woman exercising"></div>
  <h2 class="section-title">What we are</h2>
  <div class="card" style="left:77px;width:333px">
    <div class="photo ph-run" role="img" aria-label="Photo of people running on treadmills"></div>
    <div class="card-label">Health</div>
    <div class="card-icon"><svg width="48" height="48" viewBox="0 0 48 48" fill="none" stroke="#1b4a0b" stroke-width="3"><path d="M24 40 C8 28 4 20 8 13 C12 6 20 7 24 14 C28 7 36 6 40 13 C44 20 40 28 24 40Z"/><polyline points="8,24 17,24 20,18 25,30 28,24 40,24"/></svg></div>
  </div>
  <div class="card" style="left:432px;width:336px">
    <div class="photo ph-pilates" role="img" aria-label="Photo of a pilates class on reformer machines"></div>
    <div class="card-label">Wellness</div>
    <div class="card-icon"><svg width="48" height="48" viewBox="0 0 48 48" fill="none" stroke="#1b4a0b" stroke-width="3"><circle cx="24" cy="24" r="11"/><polyline points="24,17 24,24 29,27"/><g stroke-width="2.5"><line x1="24" y1="4" x2="24" y2="9"/><line x1="24" y1="39" x2="24" y2="44"/><line x1="4" y1="24" x2="9" y2="24"/><line x1="39" y1="24" x2="44" y2="24"/><line x1="10" y1="10" x2="13" y2="13"/><line x1="35" y1="35" x2="38" y2="38"/><line x1="38" y1="10" x2="35" y2="13"/><line x1="13" y1="35" x2="10" y2="38"/></g></svg></div>
  </div>
  <div class="card" style="left:790px;width:333px">
    <div class="photo ph-train" role="img" aria-label="Photo of a trainer with a client in the gym"></div>
    <div class="card-label">Fitness</div>
    <div class="card-icon"><svg width="48" height="48" viewBox="0 0 48 48" fill="#1b4a0b"><circle cx="30" cy="9" r="4"/><path d="M18 20 L28 15 L33 26 L40 28 L39 31 L30 29 L27 23 L22 26 L26 34 L23 36 L16 26Z"/><rect x="6" y="38" width="36" height="4" rx="2"/></svg></div>
  </div>
</section>

<section class="team">
  <h2 class="section-title">Our Team Expert</h2>
  <div class="member" style="left:77px">
    <svg class="shape" width="293" height="353" viewBox="0 0 293 353"><polygon points="0,0 293,0 218,353 75,353" fill="#1b4a0b"/><path d="M56 353 A90 90 0 0 1 236 353Z" fill="#c8f09c"/></svg>
    <div class="member-name">Owen Castrell</div>
    <div class="member-role">Founder and owner of<br>Brightmarch</div>
    <div class="socials"><i></i><i></i><i></i><i></i></div>
    <div class="photo" role="img" aria-label="Photo of the team member in a black training shirt"></div>
  </div>
  <div class="member" style="left:453px">
    <svg class="shape" width="293" height="353" viewBox="0 0 293 353"><polygon points="0,0 293,0 218,353 75,353" fill="#1b4a0b"/><path d="M56 353 A90 90 0 0 1 236 353Z" fill="#c8f09c"/></svg>
    <div class="member-name">Owen Castrell</div>
    <div class="member-role">Founder and owner of<br>Brightmarch</div>
    <div class="socials"><i></i><i></i><i></i><i></i></div>
    <div class="photo" role="img" aria-label="Photo of the team member in a sleeveless training top"></div>
  </div>
  <div class="member" style="left:830px">
    <svg class="shape" width="293" height="353" viewBox="0 0 293 353"><polygon points="0,0 293,0 218,353 75,353" fill="#1b4a0b"/><path d="M56 353 A90 90 0 0 1 236 353Z" fill="#c8f09c"/></svg>
    <div class="member-name">Owen Castrell</div>
    <div class="member-role">Founder and owner of<br>Brightmarch</div>
    <div class="socials"><i></i><i></i><i></i><i></i></div>
    <div class="photo" role="img" aria-label="Photo of the team member in a black training shirt"></div>
  </div>
</section>

<section class="stats">
  <div class="stat" style="left:201px"><b>261</b><span>Cup of Tea</span></div>
  <div class="stat" style="left:467px"><b>500</b><span>Award Win</span></div>
  <div class="stat" style="left:735px"><b>11,500</b><span>Happy Clients</span></div>
  <div class="stat" style="left:1021px"><b>150</b><span>Fitness Course</span></div>
</section>

<section class="split">
  <div class="event">
    <div class="photo" role="img" aria-label="Dark photo of an outdoor fitness event"></div>
    <div class="event-tint"></div>
    <h2 class="half-title" style="left:0">Up Coming Event</h2>
    <p class="half-text" style="left:0">Lorem Ipsum is simply dummy text of the printing and typesetting industry.<br>Lorem Ipsum has been the industry's standard dummy.</p>
    <div class="event-card">
      <div class="event-date"><b>26</b><span>October</span></div>
      <div class="event-info">
        <h3>Annual Meetup 2017</h3>
        <p>Lorem Ipsum is simply dummy text of the printing and typesetting industry.</p>
        <span class="btn-dark">Join Now</span>
      </div>
    </div>
  </div>
  <div class="appoint">
    <div class="photo" role="img" aria-label="Photo of people doing a group workout with ropes"></div>
    <div class="appoint-tint"></div>
    <h2 class="half-title" style="left:600px">Make Appointment</h2>
    <p class="half-text" style="left:600px">Lorem Ipsum is simply dummy text of the printing and typesetting industry.<br>Lorem Ipsum has been the industry's standard dummy.</p>
    <div class="field" style="left:693px;top:187px;width:206px">First Name*</div>
    <div class="field" style="left:909px;top:187px;width:209px">Last Name*</div>
    <div class="field" style="left:693px;top:242px;width:206px">Email*</div>
    <div class="field" style="left:909px;top:242px;width:209px">Phone*</div>
    <div class="field" style="left:693px;top:299px;width:425px;height:49px;border-radius:25px">Comment</div>
    <div class="submit">Submit</div>
  </div>
</section>

<section class="blog">
  <h2 class="section-title">Recent Blog</h2>
  <article class="post" style="left:77px">
    <div class="photo ph-b1" role="img" aria-label="Photo of a woman doing a floor exercise"><div class="post-date">11<small>Oct</small></div></div>
    <h4>Lorem Ipsum is simply dummy</h4>
    <p>Lorem Ipsum is simply dummy text of the printing and typesetting industry. Lorem has been the industry's standard dummy.</p>
  </article>
  <article class="post" style="left:433px">
    <div class="photo ph-b2" role="img" aria-label="Photo of a man lifting weights on a bench"><div class="post-date">11<small>Oct</small></div></div>
    <h4>Lorem Ipsum is simply dummy</h4>
    <p>Lorem Ipsum is simply dummy text of the printing and typesetting industry. Lorem has been the industry's standard dummy.</p>
  </article>
  <article class="post" style="left:790px">
    <div class="photo ph-b3" role="img" aria-label="Photo of a woman training in a gym"><div class="post-date">11<small>Oct</small></div></div>
    <h4>Lorem Ipsum is simply dummy</h4>
    <p>Lorem Ipsum is simply dummy text of the printing and typesetting industry. Lorem has been the industry's standard dummy.</p>
  </article>
</section>

<section class="contact">
  <div class="photo map" role="img" aria-label="Street map showing the office location"></div>
  <div class="contact-panel">
    <h3>Get in Touch</h3>
    <ul class="contact-list">
      <li><svg width="16" height="20" viewBox="0 0 16 20" fill="#fff"><path d="M8 0a7 7 0 0 0-7 7c0 5 7 13 7 13s7-8 7-13a7 7 0 0 0-7-7zm0 10a3 3 0 1 1 0-6 3 3 0 0 1 0 6z"/></svg><span>Marven Holt<br>The Lanes Harrowfield UK &amp; Ireland</span></li>
      <li><svg width="16" height="16" viewBox="0 0 16 16" fill="#fff"><path d="M3 0l3 4-2 2c1 2 3 4 6 6l2-2 4 3-2 3C7 16 0 9 0 3z"/></svg><span>07000-114552</span></li>
      <li><svg width="16" height="16" viewBox="0 0 16 16" fill="#fff"><path d="M0 3h16v10H0z"/><path d="M0 3l8 6 8-6" fill="none" stroke="#1b4a0b" stroke-width="1.5"/></svg><span>info@marvenholt.com</span></li>
      <li><svg width="16" height="16" viewBox="0 0 16 16" fill="none" stroke="#fff" stroke-width="1.5"><circle cx="8" cy="8" r="7"/><ellipse cx="8" cy="8" rx="3" ry="7"/><line x1="1" y1="8" x2="15" y2="8"/></svg><span>www.marvenholt.com</span></li>
      <li><svg width="16" height="16" viewBox="0 0 16 16"><circle cx="8" cy="8" r="7" fill="none" stroke="#fff" stroke-width="1.5"/></svg><span>Marvenholt</span></li>
    </ul>
  </div>
</section>

<footer class="footer">
  <div class="brand"><div class="brand-name" style="font-size:28px">Marven Holt</div><div class="brand-tag">Health, Wellness, Fitness, Consultants</div></div>
  <div class="footer-social"><i></i><i></i><i></i><i></i><i></i></div>
  <div class="copyright">Copyright | Marven Holt All Rights Reserved.</div>
</footer>

</body>
</html>
```